Business Card design for a mini spa

business card for a small natural skincare/waxing spa. I need a modern, clean, classy card that draws people in but also need to be able to write future appointments on one side of it.

Target Market(s)

women age 16-70

Industry/Entity Type

Beauty Salon

Contact Information for Business Card

Brisk Skin Care 907-318-2956
2863 W Maltby Kodiak, AK 99608
Facial, Waxing, Spray Tanning,

Colors
33b8a4

Requirements
Must have
• Brisk logo with flower
• my tag line "calm hands, bright days"
• 907-318-2956
• 2863 W Maltby
• a place to write ......Your Next Appointment
• Marta Quennell
Nice to have
• something modern, elegant, clean and simple with my attached logo. I also attached a few pictures of what I like along with a color pallet and a few fonts that I like.
Should not have
• no pictures of people in a spa I do not want your typical spa pictures like stone, people receiving a treatment.

```html
<!DOCTYPE html>
<html lang="en">
<head>
<meta charset="utf-8">
<title>Brisk Skin Care – Business Card</title>
<link href="https://fonts.googleapis.com/css2?family=Amatic+SC:wght@400;700&display=swap" rel="stylesheet">
<style>
  :root {
    --stage: #2e2e2e;
    --paper: #ffffff;
    --teal: #6fcac3;
    --teal-soft: #a3ddd9;
    --teal-pale: #dff3f1;
    --teal-text: #7fd0ca;
    --white: #ffffff;
  }
  * { box-sizing: border-box; margin: 0; padding: 0; }
  html, body {
    width: 1200px;
    height: 900px;
    overflow: hidden;
    background: var(--stage);
    font-family: "Amatic SC", cursive;
  }
  .canvas {
    position: relative;
    width: 1200px;
    height: 900px;
    display: flex;
    justify-content: center;
    align-items: center;
    gap: 60px;
  }
  .card {
    width: 340px;
    height: 595px;
    background: var(--paper);
    position: relative;
    overflow: hidden;
  }
  /* Back side */
  .card-back .pattern-area {
    position: absolute;
    inset: 0;
    background: radial-gradient(circle at 50% 50%, var(--white) 0%, var(--teal-pale) 45%, #c9ebe8 100%);
  }
  /* Front side */
  .brand {
    position: absolute;
    top: 34px;
    left: 0;
    right: 0;
    text-align: center;
    color: var(--teal);
    font-weight: 400;
  }
  .brand-name {
    display: flex;
    justify-content: center;
    align-items: center;
    gap: 12px;
    font-size: 74px;
    line-height: 1;
    letter-spacing: 6px;
  }
  .brand-dot {
    width: 16px;
    height: 16px;
    border-radius: 50%;
    background: var(--teal);
  }
  .brand-sub {
    font-size: 30px;
    letter-spacing: 4px;
    line-height: 1;
    margin-top: 2px;
  }
  .tagline {
    position: absolute;
    top: 170px;
    left: 0;
    right: 0;
    text-align: center;
    color: var(--teal-text);
    font-size: 27px;
    letter-spacing: 1.5px;
  }
  .contact-band {
    position: absolute;
    top: 222px;
    left: 0;
    right: 0;
    height: 120px;
    background: var(--teal-soft);
    display: flex;
    flex-direction: column;
    justify-content: center;
    padding-left: 64px;
    gap: 6px;
    color: var(--white);
    font-size: 36px;
    letter-spacing: 1px;
  }
  .contact-line {
    display: flex;
    align-items: center;
    gap: 16px;
    line-height: 1;
  }
  .contact-line svg { width: 22px; height: 22px; flex: none; }
  .appointment {
    position: absolute;
    top: 390px;
    left: 0;
    right: 0;
    text-align: center;
    color: var(--teal-text);
    font-size: 30px;
    letter-spacing: 1.5px;
  }
  .appointment-line {
    width: 220px;
    margin: 54px auto 0;
    border-bottom: 3px dotted var(--teal);
  }
</style>
</head>
<body>
  <main class="canvas">
    <section class="card card-back">
      <div class="pattern-area" role="img" aria-label="Repeating teal line flower pattern with a larger flower at the centre"></div>
    </section>

    <section class="card card-front">
      <header class="brand">
        <div class="brand-name"><span class="brand-dot"></span>Brisk</div>
        <div class="brand-sub">Skin Care</div>
      </header>

      <p class="tagline">calm hands, bright days</p>

      <div class="contact-band">
        <div class="contact-line">
          <svg viewBox="0 0 24 24" aria-hidden="true"><path fill="#ffffff" d="M6.6 10.8a15 15 0 0 0 6.6 6.6l2.2-2.2a1 1 0 0 1 1-.25 11.4 11.4 0 0 0 3.6.57 1 1 0 0 1 1 1V20a1 1 0 0 1-1 1A17 17 0 0 1 3 4a1 1 0 0 1 1-1h3.5a1 1 0 0 1 1 1c0 1.25.2 2.45.57 3.6a1 1 0 0 1-.25 1z"/></svg>
          <span>907-318-2956</span>
        </div>
        <div class="contact-line">
          <svg viewBox="0 0 24 24" aria-hidden="true"><path fill="#ffffff" d="M21 3 3 10.5l7.5 2.9L13.4 21z"/></svg>
          <span>2863 W Maltby</span>
        </div>
      </div>

      <div class="appointment">
        <p>Your Next Appointment</p>
        <div class="appointment-line"></div>
      </div>
    </section>
  </main>
</body>
</html>
```